Stationery for use with Ninefold Ridge reports

I would like to get a stationery design that my firm -- Ninefold Ridge Advisory -- will use as a format for reports that we send our clients. I am specifically looking for a design for use on a piece of paper or letterhead -- not business cards or envelopes.

We are an Africa based US risk intelligence and strategy firm that works with multinational corporations operating in West Africa. Our initial thinking is that we would like a color scheme consistent with our existing logo -- however we are open to other color schemes.

Also, we would like to see at least two separate versions: one with our company name and logo, the other without name and logo.

We also would like font recommendations for the stationary design.

The final design should communicate discreet professionalism and a modern approach, but it should not overshadow the words and information printed on the stationery.

Target Market(s)

Multinational corporations that currently use our products.

Font styles to use
Serif
Sans Serif

Requirements
Must have
• Sense of discreet professionalism that will not overshadow the content we put onto the stationery format.
• We would like to see designs with and without our company name/logo.
• Please suggest fonts that would work with the stationery.
Nice to have
• Ideally colors consistent with out existing logo, though we are open to and even encourage other ideas.
Should not have
• No need for business cards or envelopes.

```html
<!DOCTYPE html>
<html lang="en">
<head>
<meta charset="utf-8">
<title>Ninefold Ridge Advisory — Report Letterhead</title>
<link href="https://fonts.googleapis.com/css2?family=Lato:wght@400;700;900&display=swap" rel="stylesheet">
<style>
  :root {
    --backdrop: #cbbfba;
    --paper: #ffffff;
    --ink-teal: #1f4250;
    --accent-gold: #d9a233;
    --text-body: #2c3b44;
  }
  * { box-sizing: border-box; margin: 0; padding: 0; }
  html, body {
    width: 1200px;
    height: 784px;
    overflow: hidden;
  }
  body {
    background: var(--backdrop);
    font-family: "Lato", Arial, sans-serif;
    position: relative;
  }
  .letterhead {
    position: absolute;
    left: 338px;
    top: 22px;
    width: 523px;
    height: 740px;
    background: var(--paper);
    box-shadow: 0 6px 18px rgba(60, 40, 35, 0.18);
    overflow: hidden;
  }
  .brand {
    position: absolute;
    left: 40px;
    top: 40px;
    display: flex;
    align-items: center;
    gap: 10px;
  }
  .brand-dot {
    width: 14px;
    height: 14px;
    border-radius: 50%;
    background: var(--accent-gold);
  }
  .brand-name {
    color: var(--ink-teal);
    font-weight: 900;
    font-size: 19px;
    line-height: 1.05;
    letter-spacing: 0.2px;
  }
  .brand-name span {
    display: block;
    font-size: 19px;
  }
  .contact {
    position: absolute;
    right: 38px;
    top: 150px;
    padding-left: 14px;
    border-left: 1px solid var(--accent-gold);
    color: var(--text-body);
    font-size: 8.5px;
    line-height: 1.5;
  }
  .contact-row {
    display: flex;
    align-items: center;
    gap: 5px;
  }
  .contact-row svg {
    width: 8px;
    height: 8px;
    flex: none;
  }
  .icon-gap { padding-left: 13px; }
  .footer-wave {
    position: absolute;
    left: 0;
    bottom: 0;
    width: 523px;
    height: 150px;
  }
</style>
</head>
<body>
  <main class="letterhead">
    <header class="brand">
      <div class="brand-name">Ninefold Ridge<span>Advisory</span></div>
      <div class="brand-dot"></div>
    </header>

    <address class="contact">
      <div class="icon-gap">1234 First Line Address</div>
      <div class="icon-gap">5678 Second Line Address</div>
      <div class="contact-row">
        <svg viewBox="0 0 10 10"><path d="M2 1 L4 1 L4.5 3 L3.4 4 Q4.5 6 6 6.6 L7 5.5 L9 6 L9 8 Q5 9 1.8 5.5 Q1 3 2 1 Z" fill="var(--accent-gold)"/></svg>
        <span>(111) 999-0000</span>
      </div>
      <div class="contact-row">
        <svg viewBox="0 0 10 10"><rect x="0.5" y="2" width="9" height="6" fill="var(--accent-gold)"/><path d="M0.5 2 L5 5.5 L9.5 2" stroke="#fff" stroke-width="0.8" fill="none"/></svg>
        <span>info@yourmail.com</span>
      </div>
      <div class="contact-row">
        <svg viewBox="0 0 10 10"><circle cx="5" cy="5" r="4.3" fill="none" stroke="var(--accent-gold)" stroke-width="1.2"/><circle cx="5" cy="5" r="1.6" fill="var(--accent-gold)"/></svg>
        <span>www.yourwebsite.com</span>
      </div>
    </address>

    <svg class="footer-wave" viewBox="0 0 523 150" aria-hidden="true">
      <path d="M0 86 C 30 84 55 100 110 120 C 190 140 330 142 523 150 L523 150 L0 150 Z" fill="var(--ink-teal)"/>
      <path d="M8 76 C 40 76 62 92 112 112 C 195 133 335 137 523 146" fill="none" stroke="var(--accent-gold)" stroke-width="2.5"/>
    </svg>
  </main>
</body>
</html>
```